New hardcover book cover

I want a striking, eye-catching cover with title, subtitle and a picture.See for previous book covers: www.brightquillpress.com

Target Market(s)

young, successful entrepreneurs that have built a business in a niche market that they discovered.

Font styles to use
Serif

Colors

Designer to choose colors to be used in the design.

Requirements
Must have
• A book cover that impresses and captures the imagination of those who look at it.
• MY MISTAKE, SORRY.
• Title: Founders Behind the Quiet Trade Boom
• Subtitle: 25 stories of success from
• discovering hidden opportunities
• Author: Dennis Harlow
• Please use the photo attached, thanks.

```html
<!DOCTYPE html>
<html lang="en">
<head>
<meta charset="utf-8">
<title>Founders Behind the Quiet Trade Boom — Dennis Harlow</title>
<link rel="stylesheet" href="https://fonts.googleapis.com/css2?family=Bebas+Neue&family=Josefin+Sans:wght@300&display=swap">
<style>
  :root {
    --cover-black: #000000;
    --ink-light: #e9e9e9;
    --accent-red: #e3221f;
    --soft-white: #f4dede;
  }
  html, body {
    margin: 0;
    padding: 0;
    overflow: hidden;
    background: var(--cover-black);
  }
  .book-cover {
    position: relative;
    width: 765px;
    height: 1200px;
    background: var(--cover-black);
    overflow: hidden;
  }
  .author-name {
    position: absolute;
    top: 84px;
    left: 0;
    width: 100%;
    margin: 0;
    text-align: center;
    font-family: "Josefin Sans", sans-serif;
    font-weight: 300;
    font-size: 44px;
    letter-spacing: 9px;
    color: var(--ink-light);
    text-transform: uppercase;
  }
  .cover-artwork {
    position: absolute;
    left: 202px;
    top: 262px;
    width: 360px;
    height: 350px;
    border-radius: 50%;
    background: radial-gradient(circle at 50% 50%, var(--soft-white) 0%, var(--accent-red) 70%);
  }
  .book-title {
    position: absolute;
    top: 684px;
    left: 0;
    width: 100%;
    margin: 0;
    text-align: center;
    font-family: "Bebas Neue", sans-serif;
    font-weight: 400;
    color: var(--ink-light);
    text-transform: uppercase;
    line-height: 0.86;
  }
  .title-line {
    display: block;
    font-size: 98px;
  }
  .title-line--stacked {
    display: flex;
    justify-content: center;
    align-items: center;
    gap: 8px;
  }
  .title-connector {
    display: flex;
    flex-direction: column;
    font-size: 40px;
    line-height: 0.9;
    text-align: right;
  }
  .title-line--accent {
    color: var(--accent-red);
    font-size: 124px;
  }
  .book-subtitle {
    position: absolute;
    top: 1082px;
    left: 0;
    width: 100%;
    margin: 0;
    text-align: center;
    font-family: "Josefin Sans", sans-serif;
    font-weight: 300;
    font-size: 22px;
    line-height: 1.4;
    letter-spacing: 2px;
    color: var(--ink-light);
    text-transform: uppercase;
  }
</style>
</head>
<body>
  <main class="book-cover">
    <p class="author-name">Dennis Harlow</p>

    <div class="cover-artwork" role="img" aria-label="Cover illustration: red and white archery target with an arrow in the bullseye"></div>

    <h1 class="book-title">
      <span class="title-line">Founders</span>
      <span class="title-line title-line--stacked">
        <span class="title-connector"><span>Behind</span><span>The</span></span>
        <span>Quiet</span>
      </span>
      <span class="title-line">Trade</span>
      <span class="title-line title-line--accent">Boom</span>
    </h1>

    <p class="book-subtitle">25 stories of success from<br>discovering hidden opportunities</p>
  </main>
</body>
</html>
```